Podiatry clinic requires a modern revamp and editing of existing website.

I would like a fresh new look and updated information for my current business website. An easy to navigate site with prominent address and phone number for call to action. We are a podiatry clinic that focuses on general and sports podiatry.
I would like 4 pages; including Home page, About Us, Services & Contact.
www.brambleridgepodiatry.net

Target Market(s)

Active working professionals.

Industry/Entity Type

Medical

Coding

Coded - Design and coding required

Number of Pages Required

4 page

Font styles to use
Sans Serif

Colors
6b449b

Requirements
Must have
• A modern look with logo and active images; clean and uncluttered. Visible phone number and address for call to action.
• 4 pages - Home, About Us, Services, Contact.
• Home page - update address & service logos.
• About Us - update of personal information.
• Services - Revamp of existing page.
• Contact page to include Google map, email & phone number.
Nice to have
• Ability to add content easily; eg. a blog or adding video onto Home page.
• Link to Friendpage page.

```html
<!DOCTYPE html>
<html lang="en">
<head>
<meta charset="utf-8">
<title>Bramble Ridge Podiatry</title>
<link href="https://fonts.googleapis.com/css2?family=Lato:wght@400;700&family=Open+Sans:wght@400;600;700&family=Raleway:wght@400;500&display=swap" rel="stylesheet">
<style>
:root{
  --purple:#4a3192;
  --purple-band:#4b3598;
  --purple-btn:#4a3193;
  --green:#6bbd2e;
  --white:#ffffff;
  --text:#555555;
  --muted:#888888;
  --footer-bar:#5b3fa6;
  --footer-logo:#b7a9dd;
}
*{box-sizing:border-box;margin:0;padding:0}
html,body{width:1200px;height:2727px;overflow:hidden}
body{font-family:"Open Sans",Arial,sans-serif;color:var(--text);background:var(--white);position:relative}
.abs{position:absolute}
a{color:inherit;text-decoration:none}

.topbar{top:0;left:0;width:1200px;height:52px;background:var(--purple);color:var(--white);font-size:22px;display:flex;align-items:center;justify-content:space-between;padding:0 80px 0 98px;z-index:4}
.topbar span{display:flex;align-items:center;gap:10px}

.header{top:52px;left:0;width:1200px;height:135px;background:var(--white)}
.logo-disc{top:52px;left:75px;width:200px;height:203px;background:var(--white);border-radius:0 0 100px 100px;z-index:3;display:flex;flex-direction:column;align-items:center;justify-content:center;gap:10px;padding-bottom:20px}
.logo-name{font-family:"Open Sans",sans-serif;font-weight:700;font-size:27px;line-height:1.15;color:var(--purple);text-align:center}
.logo-dot{width:22px;height:22px;border-radius:50%;background:var(--purple)}
.nav{top:56px;left:410px;display:flex;gap:44px;font-family:"Open Sans",sans-serif;font-size:19px;color:#666;text-transform:uppercase}
.nav .active{color:var(--purple)}
.header-phone{top:44px;left:890px;display:flex;align-items:center;gap:14px;font-size:26px;font-weight:700;color:var(--green)}
.phone-circle{width:54px;height:54px;border-radius:50%;background:var(--purple);display:flex;align-items:center;justify-content:center}

.hero{top:187px;left:0;width:1200px;height:573px;background:linear-gradient(100deg,#6a56a6 0%,#8a79b8 40%,#9c8cc0 62%,#5e4a93 100%)}
.hero-title{top:130px;left:80px;font-family:"Lato",sans-serif;font-weight:700;font-size:47px;line-height:77px;color:var(--white)}
.hero-sub{top:281px;left:80px;width:380px;font-size:21px;line-height:30px;color:var(--white)}
.hero-btn{top:398px;left:78px;width:228px;height:60px;border-radius:30px;background:var(--purple-btn);color:var(--white);font-family:"Raleway",sans-serif;font-size:25px;display:flex;align-items:center;justify-content:center}

.appoint{top:760px;left:0;width:1200px;height:136px;background:var(--purple-band);color:var(--white)}
.appoint-left{top:48px;left:80px;font-family:"Raleway",sans-serif;font-size:35px}
.appoint-call{top:24px;left:604px;display:flex;align-items:center;gap:12px;font-family:"Raleway",sans-serif;font-size:31px}
.appoint-call b{font-family:"Open Sans",sans-serif;font-size:31px;font-weight:700}
.ring{width:52px;height:52px;border:2px solid var(--white);border-radius:50%;display:flex;align-items:center;justify-content:center;flex:none}
.appoint-mail{top:86px;left:604px;font-size:22px;display:flex;align-items:center;gap:8px}

.treat{top:928px;display:flex;gap:24px;width:545px}
.treat-photo{width:182px;height:182px;border-radius:50%;flex:none;border:2px solid #ddd;background:radial-gradient(circle at 50% 55%,#f2d6c6 0%,#d8c2bf 55%,#b9b6c8 100%)}
.treat h2{font-family:"Raleway",sans-serif;font-weight:400;font-size:28px;color:var(--purple);margin:10px 0 12px;white-space:nowrap}
.treat p{font-size:15px;line-height:26px;color:#666}
.readmore{display:inline-flex;align-items:center;gap:4px;margin-top:12px;font-weight:700;font-size:17px;color:var(--purple)}

.welcome{top:1155px;left:0;width:1200px;height:218px;background:var(--purple-band);color:var(--white);text-align:center;overflow:hidden}
.welcome-img{top:0;left:0;width:155px;height:218px;background:linear-gradient(160deg,#e9c9b6,#c9705c 70%,#b54b3e);clip-path:polygon(0 0,55% 0,100% 45%,85% 100%,0 100%)}
.welcome h2{top:46px;left:0;width:1200px;font-family:"Raleway",sans-serif;font-weight:400;font-size:43px}
.welcome p{top:116px;left:210px;width:790px;font-size:16px;line-height:25px}

.news-title{top:1420px;left:0;width:1200px;text-align:center;font-family:"Raleway",sans-serif;font-weight:400;font-size:43px;color:#555}
.news-title span{color:var(--purple)}
.news{top:1486px;width:236px}
.news-img{width:236px;height:146px;border:1px solid #ddd}
.news h3{font-weight:400;font-size:17px;line-height:25px;color:var(--purple);margin-top:14px}
.news .date{display:flex;align-items:center;gap:6px;font-size:14px;color:var(--muted);margin:4px 0 6px}
.news p{font-size:15px;line-height:25px;color:#666}

.about{top:1880px;left:0;width:1200px;height:365px;background:var(--purple-band);color:var(--white)}
.video{top:60px;left:78px;width:432px;height:241px;background:linear-gradient(135deg,#d4d4d4,#9e9e9e);display:flex;align-items:center;justify-content:center}
.play{width:58px;height:58px;border-radius:50%;border:3px solid var(--white);display:flex;align-items:center;justify-content:center;padding-left:4px}
.about h2{top:54px;left:546px;font-family:"Raleway",sans-serif;font-weight:400;font-size:43px}
.about p{left:546px;width:580px;font-size:16px;line-height:25px}

.partners{top:2245px;left:0;width:1200px;height:173px;display:flex;align-items:center;justify-content:space-around;padding:0 60px}
.badge{height:76px;border-radius:8px}

.footer{top:2418px;left:0;width:1200px;height:258px;background:var(--purple-band);color:var(--white)}
.footer-logo{top:46px;left:84px;font-weight:700;font-size:30px;line-height:1.3;color:var(--footer-logo)}
.fcol{top:32px}
.fcol h4{font-family:"Raleway",sans-serif;font-weight:400;font-size:22px;margin-bottom:14px}
.fcol li{list-style:none;font-size:17px;line-height:36px;display:flex;align-items:center;gap:10px}
.fcol .row{display:flex;gap:10px;font-size:16px;line-height:25px;margin-bottom:10px;align-items:flex-start}
.social{display:flex;align-items:center;gap:14px;font-size:17px;margin-bottom:22px}
.social .ring{width:48px;height:48px}
.copyright{top:2676px;left:0;width:1200px;height:51px;background:var(--footer-bar);color:var(--white);font-size:16px;display:flex;align-items:center;justify-content:center}
</style>
</head>
<body>

<div class="abs topbar">
  <span><svg width="18" height="26" viewBox="0 0 18 26"><path d="M9 0C4 0 0 4 0 9c0 7 9 17 9 17s9-10 9-17c0-5-4-9-9-9zm0 12a3 3 0 110-6 3 3 0 010 6z" fill="#fff"/></svg>Suite 27 / 115 Harrow Lane Bramblewood 4020</span>
  <span><svg width="12" height="12"><circle cx="6" cy="6" r="5" fill="#fff"/></svg>Friendpage</span>
</div>

<header class="abs header">
  <nav class="abs nav"><a class="active">Home</a><a>About</a><a>Services</a><a>Contact</a></nav>
  <div class="abs header-phone"><div class="phone-circle"><svg width="24" height="24" viewBox="0 0 24 24"><path d="M6.6 10.8a15 15 0 006.6 6.6l2.2-2.2c.3-.3.7-.4 1-.2 1.1.4 2.3.6 3.6.6.6 0 1 .4 1 1V20c0 .6-.4 1-1 1A17 17 0 013 4c0-.6.4-1 1-1h3.5c.6 0 1 .4 1 1 0 1.3.2 2.5.6 3.6.1.3 0 .7-.2 1z" fill="#fff"/></svg></div>1300 555 240</div>
</header>
<div class="abs logo-disc"><div class="logo-dot"></div><div class="logo-name">Bramble Ridge<br>Podiatry</div></div>

<section class="abs hero" role="img" aria-label="Runner's legs in trainers on a road at sunset">
  <h1 class="abs hero-title">QUALIFIED HEALTH<br>PROFESSIONALS</h1>
  <p class="abs hero-sub">Various foot conditions, including Sports Injuries, Orthotic Therapy &amp; Nail Surgery</p>
  <a class="abs hero-btn">CONTACT US</a>
</section>

<section class="abs appoint">
  <div class="abs appoint-left">For Appointments or Enquiries</div>
  <div class="abs appoint-call">Please call us on <span class="ring"><svg width="22" height="22" viewBox="0 0 24 24"><path d="M6.6 10.8a15 15 0 006.6 6.6l2.2-2.2c.3-.3.7-.4 1-.2 1.1.4 2.3.6 3.6.6.6 0 1 .4 1 1V20c0 .6-.4 1-1 1A17 17 0 013 4c0-.6.4-1 1-1h3.5c.6 0 1 .4 1 1 0 1.3.2 2.5.6 3.6.1.3 0 .7-.2 1z" fill="#fff"/></svg></span><b>1300 555 240</b></div>
  <div class="abs appoint-mail">Email: <svg width="20" height="15" viewBox="0 0 20 15"><rect x="1" y="1" width="18" height="13" fill="none" stroke="#fff" stroke-width="2"/><path d="M1 1l9 7 9-7" fill="none" stroke="#fff" stroke-width="2"/></svg>info@brambleridgepodiatry.net</div>
</section>

<article class="abs treat" style="left:78px">
  <div class="treat-photo" role="img" aria-label="Gloved hands examining a patient's foot"></div>
  <div><h2>General Treatment</h2><p>Nails, Corns, Callus, Warts, Skin Disorders, Heel pain / Heel Spurs / Arch pain - plantar Fasciitis</p><a class="readmore">READ MORE <svg width="18" height="14" viewBox="0 0 18 14"><path d="M2 2l5 5-5 5M9 2l5 5-5 5" fill="none" stroke="#4a3192" stroke-width="2.5"/></svg></a></div>
</article>
<article class="abs treat" style="left:630px">
  <div class="treat-photo" role="img" aria-label="Podiatrist treating a toenail with a small tool"></div>
  <div><h2>Specialised Treatments</h2><p>Diabetic Management, Nail Surgery, Biomechanical Assessment, Gait Analysis, Orthotic Therapy</p><a class="readmore">READ MORE <svg width="18" height="14" viewBox="0 0 18 14"><path d="M2 2l5 5-5 5M9 2l5 5-5 5" fill="none" stroke="#4a3192" stroke-width="2.5"/></svg></a></div>
</article>

<section class="abs welcome">
  <div class="abs welcome-img" role="img" aria-label="Hands holding a sore ankle"></div>
  <h2 class="abs">WELCOME TO BRAMBLE RIDGE PODIATRY</h2>
  <p class="abs">Bramble Ridge Podiatry is a Podiatry clinic in the heart of Bramblewood centre. We are located between Harrow &amp; Linden Streets in the Harrow Lane Business Centre / Linden Court Complex.</p>
</section>

<h2 class="abs news-title">LATEST <span>NEWS</span></h2>
<article class="abs news" style="left:78px"><div class="news-img" role="img" aria-label="Therapist stretching a patient's leg" style="background:linear-gradient(135deg,#e8e4dc,#b9aa98)"></div><h3>Lorem Ipsum is dummy text and simply printing.</h3><div class="date"><svg width="13" height="13"><rect x="1" y="2" width="11" height="10" fill="none" stroke="#888" stroke-width="1.5"/><path d="M1 5h11" stroke="#888" stroke-width="1.5"/></svg>01 August 2016</div><p>Lorem Ipsum is simply dummy text of the printing and type setting industry.</p></article>
<article class="abs news" style="left:349px"><div class="news-img" role="img" aria-label="Bare feet walking along a beach" style="background:linear-gradient(180deg,#8fa3ad,#c4a98c)"></div><h3>Lorem Ipsum is dummy text and simply printing.</h3><div class="date"><svg width="13" height="13"><rect x="1" y="2" width="11" height="10" fill="none" stroke="#888" stroke-width="1.5"/><path d="M1 5h11" stroke="#888" stroke-width="1.5"/></svg>01 August 2016</div><p>Lorem Ipsum is simply dummy text of the printing and type setting industry.</p></article>
<article class="abs news" style="left:620px"><div class="news-img" role="img" aria-label="Foot anatomy with a highlighted heel" style="background:radial-gradient(circle at 40% 60%,#e36a5a,#9db0cf 55%,#f4f4f6 85%)"></div><h3>Lorem Ipsum is dummy text and simply printing.</h3><div class="date"><svg width="13" height="13"><rect x="1" y="2" width="11" height="10" fill="none" stroke="#888" stroke-width="1.5"/><path d="M1 5h11" stroke="#888" stroke-width="1.5"/></svg>01 August 2016</div><p>Lorem Ipsum is simply dummy text of the printing and type setting industry.</p></article>
<article class="abs news" style="left:891px"><div class="news-img" role="img" aria-label="Clinician consulting with a patient" style="background:linear-gradient(135deg,#f3ece8,#d99aa2)"></div><h3>Lorem Ipsum is dummy text and simply printing.</h3><div class="date"><svg width="13" height="13"><rect x="1" y="2" width="11" height="10" fill="none" stroke="#888" stroke-width="1.5"/><path d="M1 5h11" stroke="#888" stroke-width="1.5"/></svg>01 August 2016</div><p>Lorem Ipsum is simply dummy text of the printing and type setting industry.</p></article>

<section class="abs about">
  <div class="abs video" role="img" aria-label="Video of podiatry instruments and a foot treatment"><div class="play"><svg width="18" height="20"><path d="M2 1l15 9-15 9z" fill="#fff"/></svg></div></div>
  <h2 class="abs">ABOUT PODIATRISTS</h2>
  <p class="abs" style="top:114px">Our podiatrists are fully qualified health professionals who are able to diagnose, treat, manage or help to prevent all medical conditions that affect the feet and lower limb.</p>
  <p class="abs" style="top:214px">We provide General Podiatry Treatment and some Specialised Services in relation to various foot conditions, including Sports Injuries, Orthotic Therapy and Nail Surgery.</p>
</section>

<section class="abs partners">
  <div class="badge" style="width:220px;background:#3d4fa3"></div>
  <div class="badge" style="width:236px;background:#cfcfcf"></div>
  <div class="badge" style="width:216px;background:#1f9a4a"></div>
  <div class="badge" style="width:214px;background:#1c5fa8"></div>
</section>

<footer class="abs footer">
  <div class="abs footer-logo">Bramble Ridge<br>Podiatry</div>
  <div class="abs fcol" style="left:350px"><h4>Useful Links</h4><ul>
    <li><svg width="16" height="10"><path d="M0 5h14M10 1l4 4-4 4" stroke="#fff" stroke-width="1.6" fill="none"/></svg>Home</li>
    <li><svg width="16" height="10"><path d="M0 5h14M10 1l4 4-4 4" stroke="#fff" stroke-width="1.6" fill="none"/></svg>About</li>
    <li><svg width="16" height="10"><path d="M0 5h14M10 1l4 4-4 4" stroke="#fff" stroke-width="1.6" fill="none"/></svg>Services</li>
    <li><svg width="16" height="10"><path d="M0 5h14M10 1l4 4-4 4" stroke="#fff" stroke-width="1.6" fill="none"/></svg>Contact</li></ul></div>
  <div class="abs fcol" style="left:622px;width:240px"><h4>Get In Touch</h4>
    <div class="row"><svg width="14" height="20" viewBox="0 0 18 26" style="flex:none"><path d="M9 0C4 0 0 4 0 9c0 7 9 17 9 17s9-10 9-17c0-5-4-9-9-9zm0 12a3 3 0 110-6 3 3 0 010 6z" fill="#fff"/></svg>Suite 27 / 115 Harrow Lane Bramblewood 4020</div>
    <div class="row" style="font-weight:700"><svg width="18" height="18" viewBox="0 0 24 24" style="flex:none"><path d="M6.6 10.8a15 15 0 006.6 6.6l2.2-2.2c.3-.3.7-.4 1-.2 1.1.4 2.3.6 3.6.6.6 0 1 .4 1 1V20c0 .6-.4 1-1 1A17 17 0 013 4c0-.6.4-1 1-1h3.5c.6 0 1 .4 1 1 0 1.3.2 2.5.6 3.6.1.3 0 .7-.2 1z" fill="#fff"/></svg>1300 555 240</div>
    <div class="row"><svg width="20" height="15" viewBox="0 0 20 15" style="flex:none;margin-top:5px"><rect x="1" y="1" width="18" height="13" fill="none" stroke="#fff" stroke-width="2"/><path d="M1 1l9 7 9-7" fill="none" stroke="#fff" stroke-width="2"/></svg><span>info@brambleridgepodiatry.<br>net</span></div>
  </div>
  <div class="abs fcol" style="left:890px"><h4>Follow Us</h4>
    <div class="social"><span class="ring"></span>Friendpage</div>
    <div class="social"><span class="ring"></span>Chirper</div>
  </div>
</footer>
<div class="abs copyright">© Bramble Ridge Podiatry- 2016. All Rights Reserved.</div>

</body>
</html>
```